Dorwin's Coating & Renewal Letterhead Design We want to revamp out old traditional letterhead with the new logo designs that are attached. We are working on getting all our company items from vehicles, business, cards, t-shirts, letterhead to match. This should include company colors, fonts, and flow of items that we have attached below.

Industry/Entity Type

Construction Company

Font styles to use
Sans Serif
Other font styles liked:
• Bold with outline

Colors
ec1f27
ffffff

Requirements
Must have
• Company Name: Dorwin's Coating & Renewal
• Address: 4728 SW 81st Ter Halverd cove fl 39417
• Office Number: (555) 413-2986
• Email: Dorwinrenewal@mailbrook.example
• License Number: KRT8046392
Nice to have
• Company Colors: red, white, black, and grey

```html
<!DOCTYPE html>
<html lang="en">
<head>
<meta charset="utf-8">
<title>Dorwin's Coating &amp; Renewal – Letterhead</title>
<link rel="stylesheet" href="https://fonts.googleapis.com/css2?family=Arimo:wght@400;700&family=Tinos:wght@400;700&display=swap">
<style>
  :root {
    --brand-red: #ec1f27;
    --paper: #ffffff;
    --ink: #3a3a3a;
    --ink-soft: #6b6b6b;
    --rule: #9a9a9a;
    --backdrop: #d5d9dc;
    --watermark: #f1f1f1;
  }
  * { box-sizing: border-box; margin: 0; padding: 0; }
  html, body { width: 1200px; height: 784px; overflow: hidden; }
  body {
    background: var(--backdrop);
    font-family: "Arimo", Arial, sans-serif;
    color: var(--ink);
  }
  .letterhead {
    position: absolute;
    left: 335px; top: 17px;
    width: 530px; height: 750px;
    background: var(--paper);
    box-shadow: 0 6px 18px rgba(0,0,0,.18);
    overflow: hidden;
  }
  .letterhead__top-rule {
    position: absolute; left: 0; right: 0; top: 0;
    height: 4px; background: var(--brand-red);
  }
  .brand {
    position: absolute; right: 34px; top: 30px;
    display: flex; align-items: center; gap: 8px;
  }
  .brand__mark { width: 14px; height: 14px; background: var(--brand-red); }
  .brand__name {
    font-weight: 700; font-size: 19px; line-height: 1.1;
    color: var(--brand-red); text-align: right; letter-spacing: .3px;
  }
  .watermark {
    position: absolute; left: 20px; right: 20px; top: 300px;
    text-align: center;
    font-weight: 700; font-size: 36px; line-height: 1.15;
    color: var(--watermark);
    z-index: 0;
  }
  .letter-body {
    position: absolute; left: 58px; right: 46px; top: 112px;
    font-size: 9.6px; line-height: 1.5; color: var(--ink-soft);
    z-index: 1;
  }
  .letter-body p { text-indent: 28px; margin-bottom: 12px; }
  .signature {
    position: absolute; left: 300px; top: 545px;
    width: 150px; height: 46px;
    background: linear-gradient(90deg, #f3f3f3, #e9e9e9);
    border-radius: 4px;
  }
  .contact {
    position: absolute; left: 0; right: 0; bottom: 38px;
    text-align: center; font-family: "Tinos", "Times New Roman", serif;
  }
  .contact__icons {
    display: flex; justify-content: center; align-items: center; gap: 8px;
    margin-bottom: 6px;
  }
  .contact__icons::before, .contact__icons::after {
    content: ""; width: 70px; height: 1px; background: var(--rule); margin: 0 10px;
  }
  .contact__icon { width: 14px; height: 14px; display: block; }
  .contact__address {
    color: var(--brand-red); font-weight: 700; font-size: 10.5px; margin-bottom: 3px;
  }
  .contact__line { font-size: 9.5px; color: var(--ink-soft); line-height: 1.5; }
  .contact__sep { color: var(--brand-red); margin: 0 5px; }
</style>
</head>
<body>
  <main class="letterhead">
    <div class="letterhead__top-rule"></div>

    <header class="brand">
      <div class="brand__name">Dorwin's<br>Coating &amp; Renewal</div>
      <span class="brand__mark"></span>
    </header>

    <div class="watermark" aria-hidden="true">Dorwin's<br>Coating &amp; Renewal</div>

    <section class="letter-body">
      <p>Lorem Ipsum is simply dummy text of the printing and typesetting industry. Lorem Ipsum has been the industry's standard dummy text ever since the 1500s, when an unknown printer took a galley of type and scrambled it to make a type specimen book. It has survived not only five centuries, but also the leap into electronic typesetting, remaining essentially unchanged. It was popularised in the 1960s with the release of Sheetline sheets containing Lorem Ipsum passages, and more recently with desktop publishing software like Layoutwright including versions of Lorem Ipsum.</p>
      <p>It is a long established fact that a reader will be distracted by the readable content of a page when looking at its layout. The point of using Lorem Ipsum is that it has a more-or-less normal distribution of letters, as opposed to using 'Content here, content here', making it look like readable English. Many desktop publishing packages and web page editors now use Lorem Ipsum as their default model text, and a search for 'lorem ipsum' will uncover many web sites still in their infancy. Various versions have evolved over the years, sometimes by accident, sometimes on purpose (injected humour and the like).</p>
      <p>Contrary to popular belief, Lorem Ipsum is not simply random text. It has roots in a piece of classical Latin literature from 45 BC, making it over 2000 years old. Tomas Verrell, a Latin professor at Marlow Hill College in Ostland, looked up one of the more obscure Latin words, consectetur, from a Lorem Ipsum passage, and going through the cites of the word in classical literature, discovered the undoubtable source. Lorem Ipsum comes from sections 1.10.32 and 1.10.33 of "de Finibus Bonorum et Malorum" structures, to generate Lorem Ipsum which looks reasonable. The generated Lorem Ipsum is therefore always free from repetition, injected humour, or non-characteristic words etc.</p>
    </section>

    <div class="signature" role="img" aria-label="Handwritten signature of the sender"></div>

    <footer class="contact">
      <div class="contact__icons">
        <svg class="contact__icon" viewBox="0 0 14 14" aria-label="Location"><circle cx="7" cy="7" r="7" fill="var(--brand-red)"/><path d="M7 3a2.4 2.4 0 0 0-2.4 2.4C4.6 7.3 7 10.5 7 10.5s2.4-3.2 2.4-5.1A2.4 2.4 0 0 0 7 3z" fill="#fff"/><circle cx="7" cy="5.4" r=".9" fill="var(--brand-red)"/></svg>
        <svg class="contact__icon" viewBox="0 0 14 14" aria-label="Phone"><circle cx="7" cy="7" r="7" fill="var(--brand-red)"/><path d="M4.6 3.6l1.3-.3.7 1.7-.8.6a4.6 4.6 0 0 0 2.2 2.2l.6-.8 1.7.7-.3 1.3C7.4 9.2 4.8 6.6 4.6 3.6z" fill="#fff"/></svg>
        <svg class="contact__icon" viewBox="0 0 14 14" aria-label="License"><circle cx="7" cy="7" r="7" fill="var(--brand-red)"/><path d="M4.3 7.2l1.8 1.8 3.6-3.8" stroke="#fff" stroke-width="1.4" fill="none"/></svg>
        <svg class="contact__icon" viewBox="0 0 14 14" aria-label="Email"><circle cx="7" cy="7" r="7" fill="var(--brand-red)"/><rect x="3.8" y="4.6" width="6.4" height="4.8" fill="#fff"/><path d="M3.8 4.6L7 7.2l3.2-2.6" stroke="var(--brand-red)" stroke-width=".8" fill="none"/></svg>
        <svg class="contact__icon" viewBox="0 0 14 14" aria-label="Website"><circle cx="7" cy="7" r="7" fill="var(--brand-red)"/><circle cx="7" cy="7" r="3.3" stroke="#fff" stroke-width=".9" fill="none"/><path d="M3.7 7h6.6M7 3.7c-1.6 1.8-1.6 4.8 0 6.6M7 3.7c1.6 1.8 1.6 4.8 0 6.6" stroke="#fff" stroke-width=".7" fill="none"/></svg>
      </div>
      <div class="contact__address">4728 SW 81st Ter Halverd cove fl 39417</div>
      <div class="contact__line">(555) 413-2986<span class="contact__sep">|</span>License: KRT8046392</div>
      <div class="contact__line">Dorwinrenewal@mailbrook.example<span class="contact__sep">|</span>www.dorwinrenewal.example</div>
    </footer>
  </main>
</body>
</html>
```